New Business Card Design for Manufacturing

We are an engineering/manufacturing company that offers Advanced machining/assembly/engineering services, as well as innovative products for the heavy duty engine cooling markets.

We are looking to get a new business card designed that is clean and modern looking, but still fits the wide range of technical/skilled work we do.

- We hope to use this design as the base for other design work in new Presentations, web, and print work.

Industry/Entity Type

Engineering

Contact Information for Business Card

Our preferred color of blue is (RGB) 22/71/159 but can vary slightly from that color. Our content will be our Logo and full company name (Vantrell Forge Works, Inc.), company address, name, job title, phone number with extension, cell number, fax number, website, and email address on the cards.
We'd like the full company name next to the logo, but we are open to other interpretations of that layout.
Preferably, we would like the back side to be clean with just our logo, and the front to contain all of the contact information.

Colors
2f74b4
0355a3
85abd2

Requirements
Must have
• - Logo, company name, needed content - We are open to interpretation beyond that.
• - Standard size business card.
• - Horizontal orientation.
• - Enough space for lengthy names / job titles (for example, a job title could read "Directory of Human Resources" or "V.P. of Governmental Affairs"). We need this to look clean, whether the title be short (CEO) or long (as described above).

```html
<!DOCTYPE html>
<html lang="en">
<head>
<meta charset="utf-8">
<title>Vantrell Forge Works – Business Card</title>
<link href="https://fonts.googleapis.com/css2?family=Roboto:wght@400;500;700;900&display=swap" rel="stylesheet">
<style>
  :root {
    --brand-blue: #16479f;
    --card-blue: #1f5bb5;
    --card-blue-dark: #1a4fa3;
    --ink: #2b2b2b;
    --ink-soft: #4a4a4a;
    --rule: #9a9a9a;
    --paper: #ffffff;
    --backdrop: #e9e9eb;
  }
  * { box-sizing: border-box; margin: 0; padding: 0; }
  html, body { width: 1200px; height: 900px; overflow: hidden; }
  body {
    background: var(--backdrop);
    font-family: "Roboto", Arial, sans-serif;
    position: relative;
  }
  .card {
    position: absolute;
    left: 250px;
    width: 700px;
    height: 400px;
    border-radius: 22px;
    overflow: hidden;
    box-shadow: 0 6px 18px rgba(0,0,0,0.15);
  }
  /* back side */
  .card-back { top: 35px; background: var(--card-blue); }
  .card-back .pattern-field {
    position: absolute; inset: 0;
    background: linear-gradient(135deg, var(--card-blue) 0%, var(--card-blue-dark) 100%);
  }
  .card-back .back-mark {
    position: absolute;
    left: 50%; top: 50%;
    transform: translate(-50%, -50%);
    color: var(--paper);
    font-weight: 900;
    font-size: 34px;
    letter-spacing: 0.5px;
    text-transform: uppercase;
    white-space: nowrap;
  }
  /* front side */
  .card-front { top: 465px; background: var(--paper); }
  .brand-lockup {
    position: absolute;
    right: 50px; top: 48px;
    text-align: right;
  }
  .brand-name {
    color: var(--brand-blue);
    font-weight: 900;
    font-size: 30px;
    text-transform: uppercase;
    line-height: 1;
    letter-spacing: 0.3px;
  }
  .brand-tagline {
    margin-top: 8px;
    color: var(--brand-blue);
    font-weight: 700;
    font-size: 13px;
    text-transform: uppercase;
    letter-spacing: 1px;
  }
  .top-rule {
    position: absolute;
    left: 230px; right: 50px; top: 140px;
    height: 1.5px; background: var(--rule);
  }
  .person {
    position: absolute;
    left: 55px; top: 200px;
  }
  .person-name {
    color: var(--brand-blue);
    font-weight: 700;
    font-size: 26px;
  }
  .person-title {
    color: var(--ink-soft);
    font-size: 17px;
    margin-top: 2px;
  }
  .person-rule {
    width: 230px; height: 1.5px;
    background: var(--rule);
    margin: 14px 0 12px 25px;
  }
  .contact-list { list-style: none; margin-left: 25px; }
  .contact-list li {
    display: flex; align-items: center;
    color: var(--ink);
    font-size: 16px;
    line-height: 25px;
  }
  .contact-list svg { width: 15px; height: 15px; margin-right: 10px; fill: var(--brand-blue); }
  .office {
    position: absolute;
    right: 50px; top: 200px;
    text-align: right;
    color: var(--ink-soft);
    font-size: 16px;
    line-height: 25px;
  }
  .office .web-name { color: var(--brand-blue); }
</style>
</head>
<body>

<section class="card card-back">
  <div class="pattern-field" role="img" aria-label="Faint repeating company name pattern in tonal blue"></div>
  <div class="back-mark">Vantrell Forge Works</div>
</section>

<section class="card card-front">
  <div class="brand-lockup">
    <div class="brand-name">Vantrell Forge Works, Inc.</div>
    <div class="brand-tagline">Built to Endure</div>
  </div>
  <div class="top-rule"></div>

  <div class="person">
    <div class="person-name">Daniel Reyes</div>
    <div class="person-title">V.P. of Governmental Affairs</div>
    <div class="person-rule"></div>
    <ul class="contact-list">
      <li><svg viewBox="0 0 16 16"><path d="M3.5 1.5l2.5 0 1 3.5-1.6 1.2c.8 1.8 2.2 3.2 4 4l1.2-1.6 3.5 1v2.5c0 .8-.7 1.4-1.5 1.4C7 13.5 2.5 9 2 3c0-.8.7-1.5 1.5-1.5z"/></svg>555 014 3211</li>
      <li><svg viewBox="0 0 16 16"><path d="M4.5 1h7c.6 0 1 .4 1 1v12c0 .6-.4 1-1 1h-7c-.6 0-1-.4-1-1V2c0-.6.4-1 1-1zm.5 2v9h6V3H5zm3 9.8a.7.7 0 100 1.4.7.7 0 000-1.4z"/></svg>555 014 7890</li>
      <li><svg viewBox="0 0 16 16"><path d="M4 1h6l2 2v3h1c.6 0 1 .4 1 1v5c0 .6-.4 1-1 1h-1v2H4v-2H3c-.6 0-1-.4-1-1V7c0-.6.4-1 1-1h1V1zm1 1v4h6V3.5L9.5 2H5zm0 9v3h6v-3H5z"/></svg>555 014 7891</li>
      <li><svg viewBox="0 0 16 16"><path d="M1 3h14v1.2L8 8.6 1 4.2V3zm0 2.6l7 4.4 7-4.4V13H1V5.6z"/></svg>info@vantrellforge.com</li>
    </ul>
  </div>

  <address class="office" style="font-style:normal">
    Level 2, 17 Harlow Lane<br>
    Ashford, VIC 3921<br>
    www.<span class="web-name">vantrellforge</span>.com
  </address>
</section>

</body>
</html>
```